Commercial Real Estate

We need a business card design for a new commercial real estate business that specializes in apartment building brokerage. Not individual units but the entire complex. We find and represent the owners existing buildings and well as new buyers for those buildings. The design should convey trust, integrity, knowledge and growth. It should be easily read.

Target Market(s)

40 to 65 years old

Industry/Entity Type

Real Estate

```html
<!DOCTYPE html>
<html lang="en">
<head>
<meta charset="utf-8">
<title>Keystead Property Investments – Business Card</title>
<link rel="stylesheet" href="https://fonts.googleapis.com/css2?family=Oswald:wght@500&family=Open+Sans:wght@400;600&family=Roboto+Slab:wght@700&display=swap">
<style>
  :root {
    --backdrop: #e6e7e7;
    --card: #ffffff;
    --slate: #5a6968;
    --teal: #6fcac6;
    --ink: #2f3333;
    --on-slate: #ffffff;
  }
  html, body {
    margin: 0;
    width: 1200px;
    height: 900px;
    overflow: hidden;
    background: var(--backdrop);
  }
  .canvas {
    position: relative;
    width: 1200px;
    height: 900px;
  }
  .card {
    position: absolute;
    left: 150px;
    top: 193px;
    width: 900px;
    height: 514px;
    background: var(--card);
    box-shadow: 0 6px 24px rgba(0,0,0,0.12);
    overflow: hidden;
  }
  .card__art {
    position: absolute;
    inset: 0;
  }
  .brand {
    position: absolute;
    left: 60px;
    top: 200px;
    display: flex;
    align-items: center;
    gap: 10px;
  }
  .brand__square {
    width: 14px;
    height: 14px;
    background: var(--teal);
  }
  .brand__name {
    font-family: "Roboto Slab", serif;
    font-weight: 700;
    font-size: 22px;
    letter-spacing: 0.5px;
    color: var(--slate);
    white-space: nowrap;
  }
  .brand__rule {
    position: absolute;
    left: 60px;
    top: 246px;
    width: 380px;
    height: 2px;
    background: var(--teal);
  }
  .person {
    position: absolute;
    left: 60px;
    top: 262px;
  }
  .person__name {
    font-family: "Oswald", sans-serif;
    font-weight: 500;
    font-size: 44px;
    line-height: 1.1;
    letter-spacing: 0.5px;
    color: var(--slate);
    text-transform: uppercase;
    white-space: nowrap;
  }
  .person__role {
    margin-top: 2px;
    font-family: "Open Sans", sans-serif;
    font-weight: 600;
    font-size: 20px;
    letter-spacing: 1px;
    color: var(--ink);
    text-transform: uppercase;
    white-space: nowrap;
  }
  .contact {
    position: absolute;
    right: 24px;
    top: 190px;
    margin: 0;
    padding: 0;
    list-style: none;
    font-family: "Open Sans", sans-serif;
    font-size: 14px;
    color: var(--on-slate);
  }
  .contact__item {
    display: flex;
    justify-content: flex-end;
    align-items: center;
    gap: 10px;
    height: 30px;
    white-space: nowrap;
  }
  .contact__icon {
    width: 15px;
    height: 15px;
    flex: none;
  }
</style>
</head>
<body>
<main class="canvas">
  <section class="card" aria-label="Business card front">
    <svg class="card__art" viewBox="0 0 900 514" width="900" height="514" aria-hidden="true">
      <path class="card__accent" d="M 710 0 C 650 220 460 400 320 514 L 380 514 C 520 400 700 220 760 0 Z" fill="var(--teal)"/>
      <path class="card__panel" d="M 760 0 C 700 220 520 400 380 514 L 900 514 L 900 0 Z" fill="var(--slate)"/>
    </svg>

    <div class="brand">
      <span class="brand__square"></span>
      <span class="brand__name">Keystead Property Investments</span>
    </div>
    <div class="brand__rule"></div>

    <div class="person">
      <div class="person__name">Daniel Whitford</div>
      <div class="person__role">Financial Advisor</div>
    </div>

    <ul class="contact">
      <li class="contact__item">014 555 0192
        <svg class="contact__icon" viewBox="0 0 16 16"><rect x="4" y="1" width="8" height="14" rx="1.5" fill="none" stroke="#fff" stroke-width="1.5"/><line x1="7" y1="12.5" x2="9" y2="12.5" stroke="#fff" stroke-width="1.5"/></svg>
      </li>
      <li class="contact__item">014 555 0193
        <svg class="contact__icon" viewBox="0 0 16 16"><path d="M3 2 L6 2 L7 5 L5.5 6.5 C6.5 8.5 7.5 9.5 9.5 10.5 L11 9 L14 10 L14 13 C14 14 13 14.5 12 14.3 C7 13.5 2.5 9 1.7 4 C1.5 3 2 2 3 2 Z" fill="#fff"/></svg>
      </li>
      <li class="contact__item">hello@keystead.com
        <svg class="contact__icon" viewBox="0 0 16 16"><rect x="1" y="3" width="14" height="10" fill="#fff"/><path d="M1 3 L8 9 L15 3" fill="none" stroke="var(--slate)" stroke-width="1.3"/></svg>
      </li>
      <li class="contact__item">www.keysteadproperty.com
        <svg class="contact__icon" viewBox="0 0 16 16"><circle cx="8" cy="8" r="6.5" fill="none" stroke="#fff" stroke-width="1.4"/><ellipse cx="8" cy="8" rx="2.8" ry="6.5" fill="none" stroke="#fff" stroke-width="1.2"/><line x1="1.5" y1="8" x2="14.5" y2="8" stroke="#fff" stroke-width="1.2"/></svg>
      </li>
      <li class="contact__item">047,12th floor,Harbor Line Road QTR
        <svg class="contact__icon" viewBox="0 0 16 16"><path d="M8 15 C4 10 3 8 3 6 A5 5 0 0 1 13 6 C13 8 12 10 8 15 Z" fill="#fff"/><circle cx="8" cy="6" r="1.8" fill="var(--slate)"/></svg>
      </li>
    </ul>
  </section>
</main>
</body>
</html>
```